Animal Horse & Bedding Company Needs a Website Coded & Designed

We need a website for a new animal bedding and feed company that is visually grabbing and vibrant. We would like to see a website that displays trust, quality and confidence. Needs to be responsive and mobile friendly for all browsers and coded for both Android & IOS. SEO is also important.

Joomla or Wordpress – must be both desktop and mobile friendly with fast page load speed. Need the ability to edit ourselves in Wordpress or Joomla.

Full details attached below with some layout and content ideas.

Coding

Coded - Design and coding required

Number of Pages Required

5+ page

Font styles to use
Sans Serif

Requirements
Must have
• Needs to be responsive and mobile friendly for all browsers and coded for both Android & IOS. SEO is also important.

Wordpress – must be both desktop and mobile friendly with fast page load speed. Need the ability to edit ourselves in Wordpress.

Logo Colours:
Dark Brown
CMYK: 50 / 70 / 80 / 70
Pantone: 4625C

Orange
CMYK: 0 / 50 / 100 / 0
Pantone: 144C
Nice to have
• Use picture of building attached and super impose logo on building.

```html
<!DOCTYPE html>
<html lang="en">
<head>
<meta charset="utf-8">
<title>Golden Stook — Bedding &amp; Feed</title>
<link href="https://fonts.googleapis.com/css2?family=Oswald:wght@400;500;600&family=Lato:wght@400;700&display=swap" rel="stylesheet">
<style>
:root{
  --brown:#2e1a12;
  --brown-deep:#3a2218;
  --orange:#f07d1a;
  --grey-bg:#e6e3e1;
  --ink:#333;
  --white:#fff;
}
*{margin:0;padding:0;box-sizing:border-box}
html,body{width:1200px;height:3996px;overflow:hidden}
body{position:relative;background:var(--white);font-family:'Lato',sans-serif;color:var(--ink)}
.abs{position:absolute}
.head{font-family:'Oswald',sans-serif;text-transform:uppercase;font-weight:500}
.bar{position:absolute;height:4px;background:var(--orange)}

/* header */
.search{left:62px;top:16px;width:313px;height:48px;border:1px solid #ccc;border-radius:4px;display:flex;align-items:center;overflow:hidden}
.search-btn{width:48px;height:48px;background:var(--orange);display:flex;align-items:center;justify-content:center}
.search span{padding-left:18px;font-size:15px;color:#888}
.brand{left:0;width:1200px;top:14px;text-align:center}
.brand-name{font-family:'Oswald',sans-serif;font-size:36px;letter-spacing:3px;color:var(--brown);font-weight:500;text-transform:uppercase}
.brand-sub{font-family:'Oswald',sans-serif;font-size:13px;letter-spacing:9px;color:var(--brown);font-weight:500;text-transform:uppercase;margin-top:-4px}
.call{left:895px;top:16px;display:flex;align-items:center;gap:14px}
.call-icon{width:48px;height:48px;border-radius:50%;background:var(--orange);display:flex;align-items:center;justify-content:center}
.call small{display:block;font-size:12px;color:var(--orange)}
.call strong{font-family:'Oswald',sans-serif;font-size:27px;font-weight:500;color:var(--brown)}
.rule{left:62px;top:86px;width:1078px;height:2px;background:#999}
.nav{top:98px;left:0;width:1200px;height:20px;font-size:13px;font-weight:700;color:var(--brown)}
.nav a{position:absolute;text-decoration:none;color:inherit}
.nav a.on{color:var(--orange)}
.social-top span{position:absolute;top:100px;width:12px;height:12px;border-radius:50%;background:var(--brown)}

/* hero */
.hero{left:0;top:135px;width:1200px;height:598px;background:radial-gradient(ellipse at 50% 55%,#c07a2c 0%,#7a4a1e 45%,#3a2412 100%)}
.hero h1{position:absolute;left:0;width:1200px;top:168px;text-align:center;font-family:'Oswald',sans-serif;font-size:46px;line-height:50px;color:var(--white);font-weight:600;text-transform:uppercase}
.hero p{position:absolute;left:260px;width:680px;top:282px;text-align:center;font-size:17px;line-height:30px;color:#f5eee6}
.hero .cta{position:absolute;left:469px;top:373px;width:262px;height:47px;border-radius:8px;background:var(--orange);color:var(--white);font-family:'Oswald',sans-serif;font-size:17px;font-weight:500;display:flex;align-items:center;justify-content:center;text-transform:uppercase}
.arrow{position:absolute;top:280px;width:38px;height:38px;border-radius:50%;background:var(--orange);display:flex;align-items:center;justify-content:center}

/* welcome */
.welcome-title{left:112px;top:818px;font-size:37px;color:var(--brown)}
.welcome-text{left:112px;top:912px;width:498px;font-size:17px;line-height:30px;text-align:justify;color:#3a3a3a}
.welcome-mark{left:725px;top:838px;width:305px;text-align:center}
.welcome-mark .ring{width:260px;height:260px;margin:0 auto 24px;border-radius:50%;border:14px solid var(--brown)}
.welcome-mark .name{font-family:'Oswald',sans-serif;font-size:34px;font-weight:500;letter-spacing:3px;color:var(--brown);text-transform:uppercase}

/* values */
.values{left:0;top:1342px;width:1200px;height:555px;background:var(--grey-bg)}
.values h2{position:absolute;left:0;width:1200px;top:88px;text-align:center;font-size:38px;color:var(--brown)}
.value{position:absolute;top:199px;width:300px;text-align:center}
.value-icon{width:152px;height:152px;margin:0 auto;border-radius:50%;border:3px solid var(--brown);padding:6px}
.value-icon div{width:100%;height:100%;border-radius:50%;background:var(--orange);display:flex;align-items:center;justify-content:center}
.value h3{margin-top:20px;font-size:18px;color:var(--brown)}
.value p{margin-top:12px;font-size:15px;line-height:30px;color:#444}

/* bedding */
.bed-photo{left:0;top:1897px;width:600px;height:541px;background:linear-gradient(120deg,#e7b88a 0%,#a8551f 40%,#5a2a12 75%,#2e150a 100%)}
.bed-panel{left:600px;top:1897px;width:600px;height:541px;background:var(--brown)}
.bed-title{left:661px;top:2012px;font-size:36px;color:var(--orange)}
.ticks{list-style:none;position:absolute}
.ticks li{height:30px;display:flex;align-items:center;gap:18px;font-size:17px}
.ticks svg{flex:none}
.bed-list{left:661px;top:2093px;color:#f3ece6}
.outline-btn{position:absolute;width:171px;height:50px;border-radius:6px;display:flex;align-items:center;justify-content:center;font-family:'Oswald',sans-serif;font-size:17px;font-weight:500;text-transform:uppercase}
.bed-btn{left:661px;top:2323px;border:2px solid var(--white);color:var(--white)}

/* feed */
.feed-title{left:0;width:1200px;top:2568px;text-align:center;font-size:36px;color:var(--brown)}
.feed-text{left:155px;width:890px;top:2656px;text-align:center;font-size:17px;line-height:30px;color:#3a3a3a}
.feed-list{left:169px;top:2787px;color:#333}
.feed-btn{left:169px;top:3086px;border:2px solid var(--brown);color:var(--brown)}
.feed-photo{left:617px;top:2770px;width:466px;height:364px;background:linear-gradient(180deg,#f2c27a 0%,#c9782f 40%,#8a4a1f 62%,#6d8b2c 80%,#4b6b1e 100%)}

/* newsletter */
.news{left:0;top:3224px;width:1200px;height:384px;background:linear-gradient(180deg,#3d2419,#2e1a12)}
.news h2{position:absolute;left:0;width:1200px;top:84px;text-align:center;font-size:40px;color:var(--white)}
.news p{position:absolute;left:210px;width:780px;top:150px;text-align:center;font-size:16px;line-height:26px;font-weight:700;color:var(--white)}
.news .field{position:absolute;left:283px;top:223px;width:499px;height:56px;border:2px solid var(--white);border-radius:4px;font-size:12px;color:var(--white);padding-left:12px;display:flex;align-items:center}
.news .go{position:absolute;left:790px;top:223px;width:179px;height:56px;background:var(--orange);border-radius:3px;color:var(--brown);font-family:'Oswald',sans-serif;font-size:18px;font-weight:500;display:flex;align-items:center;justify-content:center;text-transform:uppercase}

/* footer */
.foot-brand{left:60px;top:3740px;width:310px;text-align:center}
.foot-brand .brand-name{font-size:40px}
.foot-brand .brand-sub{font-size:14px;letter-spacing:12px}
.foot-social span{position:absolute;top:3849px;width:36px;height:36px;border-radius:50%}
.col-title{position:absolute;top:3682px;font-size:18px;color:var(--brown)}
.col-list{position:absolute;list-style:none;top:3736px;font-size:15px;line-height:30px;color:#333}
.contact{position:absolute;left:870px;display:flex;gap:20px;font-size:15px;line-height:25px;color:#333}
.contact .dot{flex:none;width:30px;height:30px;border-radius:50%;background:var(--brown);display:flex;align-items:center;justify-content:center}
.foot-rule{left:62px;top:3935px;width:1038px;height:1px;background:#999}
.copy{left:0;width:1200px;top:3952px;text-align:center;font-family:'Oswald',sans-serif;font-size:15px;color:var(--brown)}
</style>
</head>
<body>

<header>
  <div class="abs search">
    <div class="search-btn"><svg width="16" height="16" viewBox="0 0 16 16"><circle cx="6.5" cy="6.5" r="4.5" fill="none" stroke="#fff" stroke-width="2"/><line x1="10" y1="10" x2="14" y2="14" stroke="#fff" stroke-width="2.5"/></svg></div>
    <span>Search Here</span>
  </div>
  <div class="abs brand">
    <div class="brand-name">Golden Stook</div>
    <div class="brand-sub">Bedding &amp; Feed</div>
  </div>
  <div class="abs call">
    <div class="call-icon"><svg width="20" height="20" viewBox="0 0 24 24"><path d="M6.6 10.8a15 15 0 0 0 6.6 6.6l2.2-2.2c.3-.3.7-.4 1-.2 1.1.4 2.3.6 3.6.6.6 0 1 .4 1 1V20c0 .6-.4 1-1 1C10.6 21 3 13.4 3 4c0-.6.4-1 1-1h3.5c.6 0 1 .4 1 1 0 1.3.2 2.5.6 3.6.1.3 0 .7-.2 1z" fill="#fff"/></svg></div>
    <div><small>Call Us Today</small><strong>+ 123 456 7890</strong></div>
  </div>
  <div class="abs rule"></div>
  <nav class="abs nav">
    <a class="on" style="left:135px">HOME</a>
    <a style="left:210px">ABOUT US</a>
    <a style="left:312px">BEDDING</a>
    <a style="left:410px">FEED</a>
    <a style="left:480px">NEWS &amp; STORIES</a>
    <a style="left:628px">CONTACT US</a>
  </nav>
  <div class="social-top">
    <span style="left:893px"></span><span style="left:938px"></span><span style="left:983px"></span><span style="left:1027px"></span>
  </div>
</header>

<section class="abs hero" role="img" aria-label="Cattle grazing in a golden pasture at sunset">
  <h1>We are dedicated in providing high quality<br>products and services.</h1>
  <p>Producing, buying and marketing hay and straw for x amount of years.&nbsp; Insert blub on ownership/history of key staff/owners.</p>
  <div class="cta">Request Quote Button</div>
  <div class="arrow" style="left:43px"><svg width="10" height="14" viewBox="0 0 10 14"><path d="M7 2 2 7l5 5" fill="none" stroke="#fff" stroke-width="2"/></svg></div>
  <div class="arrow" style="left:1119px"><svg width="10" height="14" viewBox="0 0 10 14"><path d="M3 2l5 5-5 5" fill="none" stroke="#fff" stroke-width="2"/></svg></div>
</section>

<section>
  <h2 class="abs head welcome-title">Welcome to Golden Stook</h2>
  <div class="bar" style="left:112px;top:880px;width:121px"></div>
  <p class="abs welcome-text">Looking for the best bedding and feed for your horse, livestock or household pet look no further.&nbsp; We use premium locally sourced straw and hay in all of our products and are committed in providing quality products and service.Your animal deserves the very best in health and comfort to keep them healthy, strong and happy.&nbsp; Our products are designed for horses, livestock (goats, cattle and sheep), small caged animals (rabbits, guinea pigs and more).The Golden Stook offers supply and delivery of fresh bedding as well as removal of waste bedding.&nbsp; Let us deliver you a container of fresh straw and haul your waste bedding away.&nbsp; A full service solution that is sustainable and responsible.</p>
  <div class="abs welcome-mark">
    <div class="ring"></div>
    <div class="name">Golden Stook</div>
  </div>
</section>

<section class="abs values">
  <h2 class="head">Our Values</h2>
  <div class="bar" style="left:539px;top:154px;width:122px"></div>
  <div class="value" style="left:102px">
    <div class="value-icon"><div><svg width="60" height="60" viewBox="0 0 60 60"><path d="M30 6 50 14v16c0 12-9 20-20 24-11-4-20-12-20-24V14z" fill="none" stroke="#fff" stroke-width="3"/><path d="M20 30l7 7 14-14" fill="none" stroke="#fff" stroke-width="4"/></svg></div></div>
    <h3 class="head">Quality Guaranteed</h3>
    <p>Grown for quality - 100% natural with no chemicals or additives</p>
  </div>
  <div class="value" style="left:446px">
    <div class="value-icon"><div><svg width="60" height="60" viewBox="0 0 60 60"><path d="M14 20h32l-4 32H18z" fill="none" stroke="#fff" stroke-width="3"/><line x1="10" y1="20" x2="50" y2="20" stroke="#fff" stroke-width="3"/></svg></div></div>
    <h3 class="head">Full Service Solution</h3>
    <p>Dedicated in providing a full service solution of bedding supply &amp; waste removal</p>
  </div>
  <div class="value" style="left:790px">
    <div class="value-icon"><div><svg width="60" height="60" viewBox="0 0 60 60"><circle cx="34" cy="20" r="11" fill="none" stroke="#fff" stroke-width="3"/><path d="M8 40h14l10 4h14l6-6" fill="none" stroke="#fff" stroke-width="3"/></svg></div></div>
    <h3 class="head">Convenient &amp; Cost Effective</h3>
    <p>Compressed bags , pellets or bulk products saving in shipping costs</p>
  </div>
</section>

<section>
  <div class="abs bed-photo" role="img" aria-label="Child resting a hand on a chestnut horse's neck"></div>
  <div class="abs bed-panel"></div>
  <h2 class="abs head bed-title">Bedding</h2>
  <div class="bar" style="left:661px;top:2071px;width:122px"></div>
  <ul class="ticks bed-list">
    <li><svg width="14" height="14" viewBox="0 0 14 14"><circle cx="7" cy="7" r="7" fill="#f07d1a"/><path d="M3.8 7.2 6 9.3l4.2-4.4" fill="none" stroke="#2e1a12" stroke-width="1.8"/></svg>100% Natural Chopped Straw</li>
    <li><svg width="14" height="14" viewBox="0 0 14 14"><circle cx="7" cy="7" r="7" fill="#f07d1a"/><path d="M3.8 7.2 6 9.3l4.2-4.4" fill="none" stroke="#2e1a12" stroke-width="1.8"/></svg>Low Dust</li>
    <li><svg width="14" height="14" viewBox="0 0 14 14"><circle cx="7" cy="7" r="7" fill="#f07d1a"/><path d="M3.8 7.2 6 9.3l4.2-4.4" fill="none" stroke="#2e1a12" stroke-width="1.8"/></svg>Chemical &amp; Additive Free</li>
    <li><svg width="14" height="14" viewBox="0 0 14 14"><circle cx="7" cy="7" r="7" fill="#f07d1a"/><path d="M3.8 7.2 6 9.3l4.2-4.4" fill="none" stroke="#2e1a12" stroke-width="1.8"/></svg>Clean &amp; Highly Absorbent</li>
    <li><svg width="14" height="14" viewBox="0 0 14 14"><circle cx="7" cy="7" r="7" fill="#f07d1a"/><path d="M3.8 7.2 6 9.3l4.2-4.4" fill="none" stroke="#2e1a12" stroke-width="1.8"/></svg>Cheaper than Wood Shavings</li>
    <li><svg width="14" height="14" viewBox="0 0 14 14"><circle cx="7" cy="7" r="7" fill="#f07d1a"/><path d="M3.8 7.2 6 9.3l4.2-4.4" fill="none" stroke="#2e1a12" stroke-width="1.8"/></svg>Economic – less used and less wasted</li>
    <li><svg width="14" height="14" viewBox="0 0 14 14"><circle cx="7" cy="7" r="7" fill="#f07d1a"/><path d="M3.8 7.2 6 9.3l4.2-4.4" fill="none" stroke="#2e1a12" stroke-width="1.8"/></svg>Environmentally Friendly – Recyclable &amp; Compostable</li>
  </ul>
  <div class="outline-btn bed-btn">Learn More</div>
</section>

<section>
  <h2 class="abs head feed-title">Feed</h2>
  <div class="bar" style="left:567px;top:2628px;width:66px"></div>
  <p class="abs feed-text">Hay cubes and pellets are made from premium hay offering a variety of animals a feed that is non-GMO and packed with natural nutrients.&nbsp; These pellets and cubes are less bulky to handle, store and ship. As well, they reduce the amount of wasted feed.</p>
  <ul class="ticks feed-list">
    <li><svg width="14" height="14" viewBox="0 0 14 14"><circle cx="7" cy="7" r="7" fill="#f07d1a"/><path d="M3.8 7.2 6 9.3l4.2-4.4" fill="none" stroke="#fff" stroke-width="1.8"/></svg>100% Natural</li>
    <li><svg width="14" height="14" viewBox="0 0 14 14"><circle cx="7" cy="7" r="7" fill="#f07d1a"/><path d="M3.8 7.2 6 9.3l4.2-4.4" fill="none" stroke="#fff" stroke-width="1.8"/></svg>Chemical &amp; Additive Free</li>
    <li><svg width="14" height="14" viewBox="0 0 14 14"><circle cx="7" cy="7" r="7" fill="#f07d1a"/><path d="M3.8 7.2 6 9.3l4.2-4.4" fill="none" stroke="#fff" stroke-width="1.8"/></svg>Available in Pellets or Cubes</li>
    <li><svg width="14" height="14" viewBox="0 0 14 14"><circle cx="7" cy="7" r="7" fill="#f07d1a"/><path d="M3.8 7.2 6 9.3l4.2-4.4" fill="none" stroke="#fff" stroke-width="1.8"/></svg>High Protein Content</li>
    <li><svg width="14" height="14" viewBox="0 0 14 14"><circle cx="7" cy="7" r="7" fill="#f07d1a"/><path d="M3.8 7.2 6 9.3l4.2-4.4" fill="none" stroke="#fff" stroke-width="1.8"/></svg>Eliminate Waste In Feeding</li>
    <li><svg width="14" height="14" viewBox="0 0 14 14"><circle cx="7" cy="7" r="7" fill="#f07d1a"/><path d="M3.8 7.2 6 9.3l4.2-4.4" fill="none" stroke="#fff" stroke-width="1.8"/></svg>Clean - Eliminates Dust From Feeding Baled Hay</li>
    <li><svg width="14" height="14" viewBox="0 0 14 14"><circle cx="7" cy="7" r="7" fill="#f07d1a"/><path d="M3.8 7.2 6 9.3l4.2-4.4" fill="none" stroke="#fff" stroke-width="1.8"/></svg>Cost Effective</li>
    <li><svg width="14" height="14" viewBox="0 0 14 14"><circle cx="7" cy="7" r="7" fill="#f07d1a"/><path d="M3.8 7.2 6 9.3l4.2-4.4" fill="none" stroke="#fff" stroke-width="1.8"/></svg>Convenient</li>
    <li><svg width="14" height="14" viewBox="0 0 14 14"><circle cx="7" cy="7" r="7" fill="#f07d1a"/><path d="M3.8 7.2 6 9.3l4.2-4.4" fill="none" stroke="#fff" stroke-width="1.8"/></svg>Less wasted feed</li>
  </ul>
  <div class="outline-btn feed-btn">Learn More</div>
  <div class="abs feed-photo" role="img" aria-label="Brown cows and a calf grazing on green grass in warm sunlight"></div>
</section>

<section class="abs news">
  <h2 class="head">Subscribe to Newsletter</h2>
  <p>Lorem ipsum dolor sit amet, consectetur adipiscing elit, sed do eiusmod tempor incididunt ut labore et dolore magna aliqua.</p>
  <div class="field">Enter The Email</div>
  <div class="go">Subscribe</div>
</section>

<footer>
  <div class="abs foot-brand">
    <div class="brand-name">Golden Stook</div>
    <div class="brand-sub">Bedding &amp; Feed</div>
  </div>
  <div class="foot-social">
    <span style="left:92px;background:#3b5998"></span>
    <span style="left:141px;background:#d6249f"></span>
    <span style="left:189px;background:#1da1f2"></span>
    <span style="left:238px;background:#e00"></span>
    <span style="left:286px;background:#e60023"></span>
  </div>

  <h4 class="head col-title" style="left:460px">Quick Links</h4>
  <div class="bar" style="left:460px;top:3713px;width:60px;height:3px"></div>
  <ul class="col-list" style="left:464px"><li>Home</li><li>About Us</li><li>Bedding</li><li>Feed</li><li>News &amp; Stories</li></ul>

  <h4 class="head col-title" style="left:657px">Important</h4>
  <div class="bar" style="left:657px;top:3713px;width:60px;height:3px"></div>
  <ul class="col-list" style="left:661px"><li>Contact Us</li><li>FAQ</li><li>Privacy policy</li><li>Term &amp; condition</li></ul>

  <h4 class="head col-title" style="left:870px">Contact Info</h4>
  <div class="bar" style="left:870px;top:3713px;width:60px;height:3px"></div>
  <div class="contact" style="top:3738px"><div class="dot"><svg width="12" height="14" viewBox="0 0 12 14"><path d="M6 13S1 8 1 5a5 5 0 0 1 10 0c0 3-5 8-5 8z" fill="#f07d1a"/></svg></div><div>123 Lorem ipsum dolor sit amet<br>consectetur adipiscing elit,</div></div>
  <div class="contact" style="top:3810px;align-items:center"><div class="dot"><svg width="12" height="12" viewBox="0 0 24 24"><path d="M6.6 10.8a15 15 0 0 0 6.6 6.6l2.2-2.2c.3-.3.7-.4 1-.2 1.1.4 2.3.6 3.6.6.6 0 1 .4 1 1V20c0 .6-.4 1-1 1C10.6 21 3 13.4 3 4c0-.6.4-1 1-1h3.5c.6 0 1 .4 1 1 0 1.3.2 2.5.6 3.6.1.3 0 .7-.2 1z" fill="#f07d1a"/></svg></div><div>123 456 7890</div></div>
  <div class="contact" style="top:3864px;align-items:center"><div class="dot"><svg width="14" height="10" viewBox="0 0 14 10"><rect width="14" height="10" rx="1" fill="#f07d1a"/><path d="M1 1l6 5 6-5" fill="none" stroke="#2e1a12" stroke-width="1.2"/></svg></div><div>info@goldenstook.com</div></div>

  <div class="abs foot-rule"></div>
  <div class="abs copy">© Copyrights 2021 Golden Stook &nbsp;|&nbsp;&nbsp; All Rights Reserved</div>
</footer>

</body>
</html>
```